Powepoint Templates From Logo

We need 3 Powerpoint templates for use in a variety of presentations we develop and customize. Primary uses of the powerpoint presentations are for printed "pitch books" describing our firm's capabilities and approach (a lot of words with some design elements that we have developed), printed presentations of the results of financial evaluations of our clients (lots of charts and graphs) and as the talking points for speeches.

The design needs to be professional and "solid" to establish that we are capable of selling your multi-million dollar business, but also be a little different to show that we are not just boring MBA's.

Our current website and other materials have been developed internally and leave a great deal to be desired. I have initiated this project to demonstrate how much our look can be improved and, if successful, I hope to do much bigger projects in the future.
Updates

This is my first project and I thaank you all for your participation. Since I am new to this, I don;t know if I am providing the help and feedback as I should. Please feel free to let me know how I can be a better customer.

Target Market(s)

professionals (lawyers, accountaants), business owners, business groups, technology people

Industry/Entity Type

Financial

Requirements
Must have
• our logo
a place where logo of client can be inserted if appropriate
templates for the following pages
title page
standard bullet narrative page
page for charts and graphs to mostly fill the page
Should not have a lot of dark solid color that has to be printed.

Nice to have
• something to perk up the color a little

```html
<!DOCTYPE html>
<html lang="en">
<head>
<meta charset="UTF-8">
<title>Bullet Narrative Slide</title>
<link href="https://fonts.googleapis.com/css2?family=Arimo:wght@400;700&family=Oswald:wght@700&display=swap" rel="stylesheet">
<style>
  :root {
    --navy: #062a5c;
    --navy-text: #0b2f63;
    --accent-blue: #c7dcf7;
    --footer-band: #e9f2fc;
    --heading: #111111;
    --body-grey: #7f7f7f;
    --white: #ffffff;
  }
  * { margin: 0; padding: 0; box-sizing: border-box; }
  html, body {
    width: 1200px;
    height: 900px;
    overflow: hidden;
    background: var(--white);
  }
  .slide {
    position: relative;
    width: 1200px;
    height: 900px;
    background: var(--white);
    font-family: "Arimo", Arial, sans-serif;
  }
  .corner-band {
    position: absolute;
    top: 0;
    left: 0;
  }
  .brand {
    position: absolute;
    top: 54px;
    left: 30px;
    display: flex;
    align-items: center;
    gap: 14px;
  }
  .brand-mark {
    width: 40px;
    height: 40px;
    border: 3px solid var(--white);
    border-radius: 6px;
  }
  .brand-name {
    color: var(--white);
    font-weight: 700;
    font-size: 28px;
    letter-spacing: 0.5px;
  }
  .project-heading {
    position: absolute;
    top: 54px;
    right: 30px;
    text-align: right;
    color: var(--navy-text);
  }
  .project-title {
    font-family: "Oswald", "Arial Narrow", sans-serif;
    font-weight: 700;
    font-size: 64px;
    line-height: 1;
    letter-spacing: 0.5px;
    text-transform: uppercase;
  }
  .project-subtitle {
    font-family: "Arimo", Arial, sans-serif;
    font-weight: 400;
    font-size: 40px;
    line-height: 1;
    margin-top: 14px;
  }
  .content {
    position: absolute;
    top: 336px;
    left: 102px;
  }
  .content-title {
    color: var(--heading);
    font-size: 42px;
    font-weight: 400;
    line-height: 1.2;
    margin-bottom: 22px;
  }
  .bullet-list {
    list-style: none;
  }
  .bullet-list li {
    position: relative;
    padding-left: 29px;
    color: var(--body-grey);
    font-weight: 700;
    font-size: 28px;
    line-height: 56px;
  }
  .bullet-list li::before {
    content: "";
    position: absolute;
    left: 8px;
    top: 25px;
    width: 8px;
    height: 8px;
    border-radius: 50%;
    background: var(--body-grey);
  }
  .footer-band {
    position: absolute;
    left: 0;
    bottom: 0;
    width: 1200px;
    height: 23px;
    background: var(--footer-band);
  }
</style>
</head>
<body>
  <div class="slide">
    <svg class="corner-band" width="860" height="260" viewBox="0 0 860 260" aria-hidden="true">
      <polygon points="0,0 840,0 0,250" fill="var(--accent-blue)"/>
      <polygon points="0,0 800,0 0,240" fill="var(--navy)"/>
    </svg>

    <div class="brand">
      <span class="brand-mark"></span>
      <span class="brand-name">NORTHGATE ADVISORY</span>
    </div>

    <header class="project-heading">
      <h1 class="project-title">Project Title Here</h1>
      <p class="project-subtitle">Sub title here</p>
    </header>

    <section class="content">
      <h2 class="content-title">Title</h2>
      <ul class="bullet-list">
        <li>Lorem ipsum dolor sit ipsum, Lorem ipsum dolor sit ipsum</li>
        <li>Lorem ipsum dolor sit ipsum, Lorem ipsum dolor sit ipsum</li>
        <li>Lorem ipsum dolor sit ipsum, Lorem ipsum dolor sit ipsum</li>
        <li>Lorem ipsum dolor sit ipsum, Lorem ipsum dolor sit ipsum</li>
      </ul>
    </section>

    <div class="footer-band"></div>
  </div>
</body>
</html>
```